Responsive Mobile Quelvo Jewelry Template

We need to adapt an existing Quelvo template to be 100% responsive and mobile friendly. Due to Quelvo rules, the template would need to be implemented only using HTML and CSS (no Javascript). The template design files and HTML/CSS files are required for this project. We prefer that it is implemented using a responsive framework such as Gridwell.

An example of our current template can be found here (diamond only):
https://www.quelvo-market.example/itm/507318829106?ViewItem=&item=507318829106

And example of our template with an additional section for gemstone:
https://www.quelvo-market.example/itm/507318826673?ViewItem=&item=507318826673

We had also somewhat recently designed our Quelvo store landing page so some consistency with this would be desired:
http://www.quelvoshops.example/MirrowCraftNV

Please also refer to our website: https://mirrowcraftnv.example/

Target Market(s)

Primarily women shopping for jewelry on Quelvo.

Industry/Entity Type

Jewelry

Coding

Coded - Design and coding required

Number of Pages Required

1 page

Font styles to use
Sans Serif

Requirements
Must have
• * A color scheme that fits with the existing template design.
• * REMOVE the product photo in the template.
• * Sections required for Description, Basic Details, and Diamond/Gemstone Details.
• * Please refer to https://pages.quelvo-market.example/sell/itemdescription/mobilefriendlyguidelines.html in particular, the template must use
Nice to have
• * Menu of links to other categories is desired in a mobile friendly way.
• * We are open to graphics for links to popular categories similar to those found on the store page.
• * Implemented using a standardized responsive framework such as Gridwell.

```html
<!DOCTYPE html>
<html lang="en">
<head>
<meta charset="utf-8">
<title>Mirrow Craft – Item Listing</title>
<link href="https://fonts.googleapis.com/css2?family=Lato:wght@400;700&family=Open+Sans:wght@400;600;700&display=swap" rel="stylesheet">
<style>
  :root{
    --page:#efeff0;
    --card:#ffffff;
    --purple:#8a6aa6;
    --purple-soft:#f3ecfb;
    --purple-band:#e6d6fa;
    --grey-head:#7a7a7a;
    --line:#c9c9c9;
    --text:#4a4a4a;
    --dark:#222222;
    --thumb:#e6e6ea;
  }
  *{box-sizing:border-box;margin:0;padding:0}
  html,body{width:722px;height:1200px;overflow:hidden;background:var(--page);font-family:"Open Sans",sans-serif;color:var(--text)}
  .card{position:absolute;left:67px;top:70px;width:588px;height:1058px;background:var(--card);box-shadow:0 0 3px rgba(0,0,0,.08)}
  .brand-band{position:absolute;left:0;top:0;width:100%;height:62px;background:linear-gradient(var(--purple-band),#fff)}
  .brand{position:absolute;left:0;top:13px;width:100%;display:flex;justify-content:center;align-items:center;gap:10px}
  .brand-mark{width:30px;height:30px;border-radius:50%;background:var(--purple);opacity:.8}
  .brand-name{font-family:"Lato",sans-serif;font-weight:400;color:var(--purple);line-height:1.05}
  .brand-name .main{display:block;font-size:19px;letter-spacing:.5px}
  .brand-name .sub{display:block;font-size:9px;letter-spacing:5px;text-align:center;color:#555}
  .nav{position:absolute;top:71px;width:100%;text-align:center;font-family:"Lato",sans-serif;font-weight:700;font-size:10px;color:var(--dark);word-spacing:1px}
  .nav span{margin:0 8px}

  .sidebar{position:absolute;left:16px;top:113px;width:216px;height:472px;border:1px solid var(--line)}
  .sidebar-head{background:var(--purple);color:#fff;font-size:10.5px;line-height:15px;padding:4px 14px;height:40px;margin:-1px -1px 0}
  .cats{margin-top:12px}
  .cat{display:flex;align-items:center;height:41.3px;padding-left:15px;font-size:8.6px;color:var(--dark)}
  .thumb{width:37px;height:37px;border-radius:50%;background:radial-gradient(circle,#f6f6f8,var(--thumb));margin-right:10px;flex:none}

  .details{position:absolute;left:248px;top:113px;width:326px;border:1px solid var(--line);border-top:none}
  .sec-head{background:var(--grey-head);color:#fff;font-family:"Lato",sans-serif;font-weight:700;font-size:11.5px;height:27px;line-height:27px;text-align:center}
  .row{display:grid;grid-template-columns:163px 1fr;height:24.2px;line-height:24px;font-size:8.3px;text-align:center;border-top:1px solid var(--line);background:#fff}
  .row.alt{background:var(--purple-soft)}
  .row div:first-child{border-right:1px solid var(--line)}
  .row a{color:var(--purple)}
  .note{height:34px;line-height:34px;text-align:center;font-style:italic;font-weight:600;font-size:9.5px;color:var(--dark);border-top:1px solid var(--line)}
  .ask{height:41px;line-height:41px;text-align:center;font-family:"Lato",sans-serif;font-weight:700;font-size:9.5px;color:var(--dark)}
  .ask svg{vertical-align:-1px;margin-right:5px}

  .description{position:absolute;left:16px;top:606px;width:558px;height:76px;border:1px solid var(--line);border-top:none}
  .description p{text-align:center;font-size:8.3px;padding-top:19px}

  .policies{position:absolute;left:16px;top:704px;width:558px;height:255px;border:1px solid var(--line);padding:0 38px 0 26px}
  .tabs{display:flex;justify-content:center;gap:20px;margin-top:27px;font-family:"Lato",sans-serif;font-weight:700;font-size:9.5px;color:var(--dark);padding-left:12px}
  .tabs .active{color:var(--purple);border-bottom:2px solid var(--purple);padding-bottom:2px}
  .ship-rate{margin-top:23px;color:var(--purple);font-size:9px}
  .ship-title{margin-top:7px;font-family:"Lato",sans-serif;font-weight:400;font-size:11.2px;color:var(--dark);letter-spacing:.3px}
  .policies p.body{margin-top:9px;font-size:8.2px;line-height:14.4px}
  .policies p.body + p.body{margin-top:14.4px}

  .badges{position:absolute;left:0;top:978px;width:100%;display:flex;justify-content:center;align-items:center;gap:44px}
  .badge-rect{width:70px;height:52px;background:#dfe4ec;border-radius:3px}
  .badge-wide{width:74px;height:44px;background:#e8e4d8;border-radius:3px}
  .badge-seal{width:66px;height:66px;border-radius:50%;background:#4a5f8a}
</style>
</head>
<body>
<main class="card">
  <header class="brand-band">
    <div class="brand">
      <span class="brand-mark"></span>
      <span class="brand-name"><span class="main">MIRROW CRAFT</span><span class="sub">NEVADA</span></span>
    </div>
  </header>
  <nav class="nav">ABOUT US<span>|</span>FAQS<span>|</span>WHY BUY FROM US<span>|</span>SAVE SELLER</nav>

  <aside class="sidebar">
    <div class="sidebar-head">Please choose a category<br>below to see more subcategories</div>
    <div class="cats">
      <div class="cat"><span class="thumb" role="img" aria-label="Diamond engagement ring photo"></span>Diamond Engagement Rings</div>
      <div class="cat"><span class="thumb" role="img" aria-label="Pink diamond ring photo"></span>Fancy Yellow &amp; Pink Diamond</div>
      <div class="cat"><span class="thumb" role="img" aria-label="Cocktail diamond ring photo"></span>Cocktail Fashion Diamond Rings</div>
      <div class="cat"><span class="thumb" role="img" aria-label="Sapphire gemstone ring photo"></span>Colored Gemstone Diamond Rings</div>
      <div class="cat"><span class="thumb" role="img" aria-label="Semi mount ring photo"></span>Semi Mount Diamond Rings</div>
      <div class="cat"><span class="thumb" role="img" aria-label="Men's diamond band photo"></span>Men's Diamond Jewelry</div>
      <div class="cat"><span class="thumb" role="img" aria-label="Diamond pendant photo"></span>Diamond Pendants</div>
      <div class="cat"><span class="thumb" role="img" aria-label="Diamond stud earrings photo"></span>Diamond Earrings</div>
      <div class="cat"><span class="thumb" role="img" aria-label="Diamond necklace photo"></span>Diamond Necklaces</div>
      <div class="cat"><span class="thumb" role="img" aria-label="Diamond bracelet photo"></span>Diamond Bracelets &amp; Bangles</div>
    </div>
  </aside>

  <section class="details">
    <div class="sec-head">Item Details</div>
    <div class="row"><div>Model Number:</div><div>MCN-RV52714BLT-310</div></div>
    <div class="row alt"><div>Metal:</div><div>14k Yellow Gold</div></div>
    <div class="row"><div>Weight:</div><div>4.08 grams</div></div>
    <div class="row alt"><div>L x W x H:</div><div>12 x 10 x 7.2 MM</div></div>
    <div class="row"><div>Style:</div><div>Halo</div></div>
    <div class="row alt"><div>Ring Size:</div><div>6 (contact us for sizing options)</div></div>
    <div class="sec-head">Diamond Details</div>
    <div class="row"><div>Total Carat Weight:</div><div>0.19 CT</div></div>
    <div class="row alt"><div>Diamond Count:</div><div>22</div></div>
    <div class="row"><div>Shape:</div><div>Round</div></div>
    <div class="row alt"><div>Color/Clarity:</div><div>G / SI1</div></div>
    <div class="row"><div>Other Shape:</div><div>Round</div></div>
    <div class="row alt"><div>Other Color/Clarity:</div><div>G / SI1</div></div>
    <div class="row"><div>Certificate:</div><div>VGL (<a href="#">CLICK FOR MORE INFO</a>)</div></div>
    <div class="note">All of our diamonds and gemstones are 100% natural!</div>
    <div class="sec-head">Questions?</div>
    <div class="ask"><svg width="10" height="8" viewBox="0 0 10 8"><rect width="10" height="8" rx="1" fill="#8a6aa6"/><path d="M0 1l5 3.5L10 1" stroke="#fff" stroke-width="1" fill="none"/></svg>ASK A QUESTION VIA EMAIL</div>
  </section>

  <section class="description">
    <div class="sec-head">Item Description</div>
    <p>Exquisite Oval Aquamarine Gemstone Surrounded By A Delicate Halo Of Diamonds Mounted In A Classic 14k Yellow Gold Setting</p>
  </section>

  <section class="policies">
    <div class="tabs"><span class="active">SHIPPING DETAILS</span><span>PRODUCT GUARANTEE</span><span>RETURN POLICY</span><span>PRIVACY POLICY</span><span>WHY US</span></div>
    <div class="ship-rate">Swiftway 2 Day: Free (U.S.A. only)</div>
    <h3 class="ship-title">WE SHIP WORLDWIDE</h3>
    <p class="body">International Buyers - Please Note: Import duties, taxes, and charges are not included in the item price or shipping cost. These charges are the buyer's responsibility. Please check with your country's customs office to determine what these additional costs will be prior to bidding or buying.</p>
    <p class="body">All packages are fully insured and require signature confirmation.</p>
    <p class="body">Once your item(s) are ready to leave our facility a shipping tracking number will be sent to you. Business days do not include Saturday, Sunday or holidays. Please be sure to inspect your package upon arrival for tampering or any damage. Rush orders are welcome. Please call for availability.</p>
  </section>

  <footer class="badges">
    <span class="badge-rect" role="img" aria-label="Accreditation badge"></span>
    <span class="badge-wide" role="img" aria-label="Gemological institute badge"></span>
    <span class="badge-seal" role="img" aria-label="Gemological laboratory seal"></span>
  </footer>
</main>
</body>
</html>
```